Stationery & Envelope Design

Executive Style looking stationery & envelope design.
Business Information:
Kestrel Ridge Homes
2875 Birchwood Lane, Fairmont, OR 97401-4180
Phone: 916.555.0142
Fax: 916.555.0187

Industry/Entity Type

Business

```html
<!DOCTYPE html>
<html lang="en">
<head>
<meta charset="utf-8">
<title>Kestrel Ridge Homes — Stationery</title>
<link rel="stylesheet" href="https://fonts.googleapis.com/css2?family=Open+Sans:wght@400;600;700&display=swap">
<style>
  :root {
    --backdrop: #ececec;
    --paper: #f7f7f7;
    --paper-shade: #eeeeee;
    --edge: #dcdcdc;
    --brand-blue: #1c4f9c;
    --brand-green: #758f1c;
    --ink-grey: #6b6b6b;
  }
  * { margin: 0; padding: 0; box-sizing: border-box; }
  html, body {
    width: 1200px;
    height: 795px;
    overflow: hidden;
    background: var(--backdrop);
    font-family: "Open Sans", Arial, sans-serif;
  }
  .canvas {
    position: relative;
    width: 1200px;
    height: 795px;
  }

  /* Envelope (back view with flap) */
  .envelope {
    position: absolute;
    left: 60px;
    top: 80px;
    width: 540px;
    height: 250px;
    background: var(--paper);
    border: 1px solid var(--edge);
    box-shadow: 0 6px 14px rgba(0,0,0,0.08);
  }
  .envelope__flap {
    position: absolute;
    left: 0;
    top: 0;
    width: 540px;
    height: 118px;
  }
  .envelope__brand {
    position: absolute;
    left: 0;
    top: 48px;
    width: 100%;
    display: flex;
    justify-content: center;
    align-items: center;
    gap: 8px;
  }

  /* Letterhead */
  .letterhead {
    position: absolute;
    left: 560px;
    top: 360px;
    width: 600px;
    height: 360px;
    background: var(--paper);
    border: 1px solid var(--edge);
    box-shadow: 0 6px 14px rgba(0,0,0,0.08);
    overflow: hidden;
  }
  .letterhead__brand {
    position: absolute;
    left: 44px;
    top: 120px;
    display: flex;
    align-items: center;
    gap: 8px;
  }
  .letterhead__contact {
    position: absolute;
    left: 44px;
    bottom: 34px;
    font-size: 9px;
    font-style: normal;
    line-height: 1.5;
    letter-spacing: 0.4px;
  }
  .contact__name {
    color: var(--brand-blue);
    font-weight: 700;
  }
  .contact__address {
    color: var(--ink-grey);
  }
  .letterhead__band {
    position: absolute;
    left: 0;
    bottom: 0;
    width: 100%;
    height: 10px;
    display: flex;
  }
  .band__blue { flex: 1; background: var(--brand-blue); }
  .band__green { flex: 1; background: var(--brand-green); }

  /* Wordmark */
  .brand__mark {
    width: 10px;
    height: 10px;
    border-radius: 50%;
    background: var(--brand-blue);
    flex: none;
  }
  .brand__name {
    color: var(--brand-blue);
    font-weight: 700;
    letter-spacing: 0.3px;
    white-space: nowrap;
  }
  .envelope .brand__name { font-size: 13px; }
  .letterhead .brand__name { font-size: 16px; }
</style>
</head>
<body>
<main class="canvas">

  <section class="envelope" aria-label="Envelope back">
    <svg class="envelope__flap" viewBox="0 0 540 118" aria-hidden="true">
      <path d="M0 0 H540 V100 Q540 118 522 118 H18 Q0 118 0 100 Z" fill="var(--paper-shade)" stroke="var(--edge)" stroke-width="1"/>
    </svg>
    <div class="envelope__brand">
      <span class="brand__mark"></span>
      <span class="brand__name">Kestrel Ridge Homes</span>
    </div>
  </section>

  <section class="letterhead" aria-label="Letterhead">
    <div class="letterhead__brand">
      <span class="brand__mark"></span>
      <span class="brand__name">Kestrel Ridge Homes</span>
    </div>
    <address class="letterhead__contact">
      <div class="contact__name">Kestrel Ridge Homes</div>
      <div class="contact__address">2875 Birchwood Lane, Fairmont, OR 97401-4180</div>
    </address>
    <div class="letterhead__band">
      <span class="band__blue"></span>
      <span class="band__green"></span>
    </div>
  </section>

</main>
</body>
</html>
```